Business Cards Design for the electrical wholesaler: clean bold dynamic :)

We need a business card design that would follow our latest brand guidelines. As an electrical wholesaler we want to bring a fresh look and feel into the industry. The design should be clean bold and dynamic. It should come alive with the renewed energy of our green colour. Our grey colour should keep things balanced and complement the notion of maturity and responsibility. We employ Lato as a corporate font however are not bound by this font and we’re open to interpretation here.

Target Market(s)

Electrical contractors

Industry/Entity Type

Business

Contact Information for Business Card

Logo
Name & Surname: Halyna Dorosh
Job Title: Director of Marketing
Email: halya.dorosh@quillmail.example
Cell phone: XXX.XXX.XXXX
Address: 20517 - 87 Ave. Edmonton, AB, Canada. T6K 4N8
Business Phone: 780.555.0184
Website: www.brovix.example

Font styles to use
Other font styles liked:
• Lato

Requirements
Must have
• Logo & website
Nice to have
• Brand elements - some of them you may find in the attached Brand Guidelines (e.g. three lines on the background signifying "W")

```html
<!DOCTYPE html>
<html lang="en">
<head>
<meta charset="utf-8">
<title>Brovix Business Cards</title>
<link rel="stylesheet" href="https://fonts.googleapis.com/css2?family=Lato:wght@400;700;900&display=swap">
<style>
  :root {
    --green: #7cc336;
    --green-light: #a4d957;
    --grey-dark: #3f4144;
    --grey-mid: #58595b;
    --white: #f7f7f7;
    --backdrop: #d9dadb;
  }
  * { margin: 0; padding: 0; box-sizing: border-box; }
  html, body { width: 1200px; height: 900px; overflow: hidden; }
  body {
    background: var(--backdrop);
    font-family: "Lato", Arial, sans-serif;
    position: relative;
  }
  .card {
    position: absolute;
    width: 640px;
    height: 366px;
    overflow: hidden;
    box-shadow: 0 10px 28px rgba(0,0,0,0.18);
  }

  /* Back of card */
  .card-back {
    left: 80px;
    top: 70px;
    background: linear-gradient(150deg, var(--green) 0%, var(--green-light) 100%);
  }
  .card-back .base-band {
    position: absolute;
    left: 0; right: 0; bottom: 0;
    height: 50px;
    background: var(--grey-mid);
  }
  .brand {
    position: absolute;
    display: flex;
    align-items: center;
    gap: 14px;
  }
  .brand-dot {
    border-radius: 50%;
    flex: none;
  }
  .brand-name {
    font-weight: 400;
    color: var(--grey-mid);
    letter-spacing: -1px;
    line-height: 1;
  }
  .card-back .brand { left: 120px; top: 120px; }
  .card-back .brand-dot { width: 54px; height: 54px; background: var(--white); }
  .card-back .brand-name { font-size: 84px; }

  /* Front of card */
  .card-front {
    left: 480px;
    top: 464px;
    background: var(--white);
  }
  .card-front .dark-panel {
    position: absolute;
    left: 0; right: 0; top: 196px; bottom: 0;
    background: var(--grey-dark);
  }
  .card-front .notch {
    position: absolute;
    left: 84px;
    top: 196px;
  }
  .card-front .green-band {
    position: absolute;
    left: 0; right: 0; bottom: 0;
    height: 46px;
    background: var(--green);
  }
  .card-front .brand { right: 40px; top: 40px; gap: 12px; }
  .card-front .brand-dot { width: 40px; height: 40px; background: var(--green); }
  .card-front .brand-name { font-size: 62px; }

  .person {
    position: absolute;
    left: 56px;
    top: 112px;
  }
  .person-name {
    font-size: 26px;
    font-weight: 900;
    color: var(--green);
    text-transform: uppercase;
    letter-spacing: 0.5px;
  }
  .person-title {
    font-size: 17px;
    color: var(--grey-mid);
    margin-top: 4px;
  }

  .address {
    position: absolute;
    right: 36px;
    top: 212px;
    width: 250px;
    font-size: 14px;
    line-height: 1.45;
    color: var(--white);
    text-align: right;
  }

  .contacts {
    position: absolute;
    left: 80px;
    top: 210px;
    list-style: none;
    font-size: 15px;
    line-height: 1.2;
    color: var(--white);
  }
  .contacts li {
    display: flex;
    align-items: center;
    gap: 12px;
    margin-bottom: 5px;
  }
  .contacts svg { width: 15px; height: 15px; flex: none; }
</style>
</head>
<body>

  <section class="card card-back" aria-label="Card back">
    <div class="brand">
      <span class="brand-dot"></span>
      <span class="brand-name">brovix</span>
    </div>
    <div class="base-band"></div>
  </section>

  <section class="card card-front" aria-label="Card front">
    <div class="dark-panel"></div>
    <svg class="notch" width="28" height="14" viewBox="0 0 28 14" aria-hidden="true">
      <polygon points="0,0 28,0 14,14" fill="var(--white)"/>
    </svg>
    <div class="green-band"></div>

    <div class="brand">
      <span class="brand-dot"></span>
      <span class="brand-name">brovix</span>
    </div>

    <div class="person">
      <div class="person-name">Halyna Dorosh</div>
      <div class="person-title">Director of Marketing</div>
    </div>

    <p class="address">20517 - 87 Ave. Edmonton, AB, Canada. T6K 4N8</p>

    <ul class="contacts">
      <li>
        <svg viewBox="0 0 16 16" aria-hidden="true"><path d="M4 1l2.5 3-1.5 1.8c.9 2 2.4 3.5 4.3 4.3L11 8.6 14.5 11 13 14C7 14 2 9 2 3z" fill="var(--green)"/></svg>
        780.555.0184
      </li>
      <li>
        <svg viewBox="0 0 16 16" aria-hidden="true"><rect x="4" y="1" width="8" height="14" rx="1.5" fill="var(--green)"/><rect x="5.5" y="3" width="5" height="8" fill="var(--grey-dark)"/><circle cx="8" cy="13" r="0.9" fill="var(--grey-dark)"/></svg>
        XXX.XXX.XXXX
      </li>
      <li>
        <svg viewBox="0 0 16 16" aria-hidden="true"><rect x="1" y="3" width="14" height="10" fill="var(--green)"/><path d="M1 3l7 6 7-6" fill="none" stroke="var(--grey-dark)" stroke-width="1.4"/></svg>
        halya.dorosh@quillmail.example
      </li>
      <li>
        <svg viewBox="0 0 16 16" aria-hidden="true"><g fill="none" stroke="var(--green)" stroke-width="1.4"><circle cx="8" cy="8" r="6.5"/><ellipse cx="8" cy="8" rx="3" ry="6.5"/><path d="M1.5 8h13M3 4.5h10M3 11.5h10"/></g></svg>
        www.brovix.example
      </li>
    </ul>
  </section>

</body>
</html>
```